VFX Company Business Card Design Project

The Kestrel Works is a decentralized Visual Effects Studio servicing the television and feature film industries.
Project Brief:
Take our logo that was previously designed on Pencil Harbor and make a double sided business card.
Requirements:
- Card MUST be double sided.
- Front of card MUST have the yellow part of our logo against the dark grey background.
- Back of card is completely up to the designer.
- Back of card must include the complete company logo.
Please follow these File Preparation guidelines:
http://printnook.ca/infopage?file=filetype_en&s=PrintNook_new&lang=en
Business

```html
<!DOCTYPE html>
<html lang="en">
<head>
<meta charset="utf-8">
<title>The Kestrel Works – Business Card</title>
<link rel="stylesheet" href="https://fonts.googleapis.com/css2?family=Fira+Sans:wght@400;500&display=swap">
<style>
  :root {
    --backdrop: #a3b1b6;
    --card-dark: #3b3b3b;
    --brand-yellow: #fdd11f;
    --text-light: #f2f2f2;
    --logo-grey: #8a8d91;
    --white: #ffffff;
  }
  * { box-sizing: border-box; margin: 0; padding: 0; }
  html, body {
    width: 1200px; height: 960px; overflow: hidden;
    background: var(--backdrop);
    font-family: "Fira Sans", sans-serif;
  }
  .sheet {
    width: 1200px; height: 960px;
    display: flex; flex-direction: column;
    align-items: center; justify-content: center; gap: 60px;
  }
  .card {
    position: relative;
    width: 700px; height: 400px;
    box-shadow: 0 10px 28px rgba(0,0,0,.25);
  }
  /* Front */
  .card--front { background: var(--card-dark); color: var(--text-light); }
  .identity {
    position: absolute; left: 44px; top: 62px;
    width: 380px; padding-bottom: 10px;
    border-bottom: 3px solid var(--brand-yellow);
  }
  .identity__name { font-size: 34px; font-weight: 400; letter-spacing: .5px; }
  .identity__role { font-size: 20px; margin-left: 6px; }
  .contact { position: absolute; left: 44px; top: 150px; list-style: none; font-size: 22px; line-height: 34px; }
  .contact__label { display: inline-block; width: 38px; color: var(--brand-yellow); font-size: 19px; }
  .address { position: absolute; left: 44px; top: 262px; font-size: 22px; line-height: 32px; font-style: normal; }
  .front-mark {
    position: absolute; right: 40px; bottom: 48px;
    color: var(--brand-yellow); font-size: 30px; font-weight: 500;
  }
  /* Back */
  .card--back {
    background: var(--brand-yellow);
    display: flex; align-items: center; justify-content: center; gap: 18px;
    overflow: hidden;
  }
  .back-mark__dot { width: 34px; height: 34px; border-radius: 50%; background: var(--white); }
  .back-mark__name { color: var(--white); font-size: 50px; font-weight: 500; letter-spacing: 1px; }
  .back-ghost {
    position: absolute; right: 30px; bottom: 24px;
    color: rgba(0,0,0,.06); font-size: 44px; font-weight: 500;
  }
</style>
</head>
<body>
<main class="sheet">
  <section class="card card--front" aria-label="Card front">
    <header class="identity">
      <span class="identity__name">MAREN HOLT</span><span class="identity__role">Managing Partner</span>
    </header>
    <ul class="contact">
      <li><span class="contact__label">t</span>(480) 555-0147</li>
      <li><span class="contact__label">e</span>name@kestrelworks.com</li>
      <li><span class="contact__label">w</span>www.kestrelworks.com</li>
    </ul>
    <address class="address">4410 Canyon Ridge Road,<br>Suite 210, Mesa Verde,<br>Arizona 85000</address>
    <div class="front-mark">The Kestrel Works</div>
  </section>

  <section class="card card--back" aria-label="Card back">
    <span class="back-mark__dot"></span>
    <span class="back-mark__name">The Kestrel Works</span>
    <span class="back-ghost" aria-hidden="true">The Kestrel Works</span>
  </section>
</main>
</body>
</html>
```